Beacon Advisory Website

I currently have a website www.beaconadvisoryinc.com. We are a IT Consulting Company. Our website will pretty much tell out our services. I am looking to enhance my website and make it look more professional. Looking for very classy and Contemporary look and design for my website.

It Company

```html
<!DOCTYPE html>
<html lang="en">
<head>
<meta charset="utf-8">
<title>Beacon Advisory</title>
<link href="https://fonts.googleapis.com/css2?family=Lato:wght@400;700;900&display=swap" rel="stylesheet">
<style>
:root{
  --sky:#0a9ad6;
  --navy:#163f82;
  --navy-dark:#10326b;
  --ink:#2d2d2d;
  --text:#333;
  --nav-bg:#3a3a3a;
  --nav-line:#2a2a2a;
  --footer:#383838;
  --white:#fff;
  --rule:#bbb;
}
*{box-sizing:border-box;margin:0;padding:0}
html,body{width:1147px;height:1200px;overflow:hidden}
body{position:relative;background:var(--white);font-family:'Lato',sans-serif;color:var(--text)}
.topbar{position:absolute;left:0;top:0;width:1147px;height:33px;background:var(--sky)}
.social-top{position:absolute;right:94px;top:0;display:flex}
.social-top span{width:35px;height:33px;background:var(--navy);border-left:1px solid #2a5aa0}
.header{position:absolute;top:33px;left:0;width:1147px;height:82px}
.brand{position:absolute;left:94px;top:25px;display:flex;align-items:center;gap:10px}
.brand-mark{width:32px;height:32px;border-radius:50%;background:var(--navy)}
.brand-name{font-weight:900;font-size:22px;color:var(--navy);letter-spacing:.5px}
.phone{position:absolute;right:94px;top:29px;display:flex;align-items:center;gap:8px;font-size:17px;color:var(--ink)}
.nav{position:absolute;top:115px;left:0;width:1147px;height:41px;background:var(--nav-bg)}
.nav ul{list-style:none;position:absolute;left:94px;display:flex;height:41px}
.nav li{height:41px;display:flex;align-items:center;justify-content:center;color:var(--white);font-size:15px;border-right:1px solid var(--nav-line)}
.nav li:last-child{border-right:0}
.nav li.active{background:var(--sky);position:relative}
.nav li.active::after{content:"";position:absolute;bottom:0;left:50%;margin-left:-5px;border:5px solid transparent;border-bottom-color:var(--white)}
.hero{position:absolute;top:156px;left:0;width:1147px;height:276px;background:linear-gradient(100deg,#1c2733 0%,#6d7e90 35%,#d9dde2 55%,#8a8a8a 75%,#4a4a4a 100%)}
.welcome{position:absolute;top:432px;left:0;width:1147px;height:174px;background:linear-gradient(90deg,var(--navy) 0%,#1f5299 50%,var(--navy-dark) 100%);color:var(--white);text-align:center}
.welcome h1{margin-top:18px;font-size:29px;font-weight:700}
.welcome .divider{position:relative;width:634px;height:1px;background:rgba(255,255,255,.7);margin:8px auto 0}
.welcome .divider::after{content:"";position:absolute;left:50%;top:0;margin-left:-9px;border:9px solid transparent;border-top:8px solid var(--white)}
.welcome p{width:950px;margin:17px auto 0;font-size:12px;font-weight:700;line-height:18.5px}
.welcome .more{position:absolute;left:555px;top:154px;width:36px;height:20px;background:var(--white);border-radius:3px 3px 0 0;color:#666;font-size:20px;line-height:20px}
.card{position:absolute;top:650px;width:295px;height:351px;border:1px solid #ddd;border-top:3px solid var(--navy);box-shadow:0 8px 10px -6px rgba(0,0,0,.15)}
.card-head{display:flex;align-items:center;gap:13px;padding:11px 0 0 13px;height:56px}
.card-icon{width:38px;height:38px;border-radius:50%;background:var(--ink);display:flex;align-items:center;justify-content:center}
.card h2{font-size:26px;font-weight:700;color:var(--ink)}
.card h2 b{color:var(--navy);font-weight:700}
.card-photo{margin:9px 0 0 13px;width:268px;height:118px}
.card p{font-size:11.5px;line-height:17.2px;letter-spacing:.1px;padding:0 10px 0 13px}
.card .photo-text{margin-top:14px}
.card .intro-text{margin-top:4px}
.card-plus{position:absolute;right:-1px;bottom:-1px;width:25px;height:25px;background:var(--navy);color:var(--white);text-align:center;font-size:22px;line-height:24px;font-weight:700}
.services{list-style:none;margin:8px 0 0 13px;width:210px}
.services li{display:flex;align-items:center;gap:11px;height:32px;font-size:13px;color:var(--ink);border-bottom:1px dotted var(--rule)}
.services li:last-child{border-bottom:0}
.footer{position:absolute;top:1057px;left:0;width:1147px;height:143px;background:var(--footer);border-top:3px solid #2a2a2a;color:var(--white)}
.footer-links{position:absolute;left:96px;top:35px;font-size:13.5px;word-spacing:1px}
.footer-links i{font-style:normal;margin:0 6px}
.newsletter{position:absolute;left:95px;top:80px;display:flex;align-items:center}
.nl-icon{width:37px;height:37px;border-radius:50%;border:2px solid var(--white);background:var(--footer);display:flex;align-items:center;justify-content:center;position:relative;z-index:1}
.nl-input{width:172px;height:37px;background:var(--white);margin-left:-10px;padding-left:20px;font-size:12px;color:#777;line-height:37px}
.nl-btn{margin-left:9px;width:98px;height:37px;background:var(--navy);font-size:14px;font-weight:700;text-align:center;line-height:37px}
.social-foot{position:absolute;left:429px;top:86px;display:flex;gap:9px}
.social-foot span{width:25px;height:25px;border-radius:50%;background:var(--white)}
.footer-brand{position:absolute;right:94px;top:30px;display:flex;align-items:center;gap:10px}
.footer-brand .brand-mark{width:40px;height:40px;background:#777}
.footer-brand .brand-name{color:#999;font-size:20px}
.copyright{position:absolute;right:96px;top:104px;font-size:12.5px}
</style>
</head>
<body>
<div class="topbar">
  <div class="social-top" aria-label="Social links"><span></span><span></span><span></span><span></span></div>
</div>

<header class="header">
  <div class="brand"><span class="brand-mark"></span><span class="brand-name">BEACON ADVISORY</span></div>
  <div class="phone">
    <svg width="25" height="25" viewBox="0 0 26 26"><circle cx="13" cy="13" r="11.5" fill="none" stroke="#163f82" stroke-width="2"/><path d="M9 7.5c-1 1-1 3 .8 6s4 4.8 5.8 4.5l1.4-1.6-2.3-2-1.2.9c-1-.6-2.1-1.9-2.6-3l1-1.1-1.7-2.5z" fill="#163f82"/></svg>
    <span>555 014 2290</span>
  </div>
</header>

<nav class="nav">
  <ul>
    <li class="active" style="width:166px">COMPANY</li>
    <li style="width:157px">SERVICES</li>
    <li style="width:174px">SOLUTIONS</li>
    <li style="width:174px">RESOURCES</li>
    <li style="width:147px">CAREER</li>
    <li style="width:141px">CONTACT US</li>
  </ul>
</nav>

<div class="hero" role="img" aria-label="Businessman holding a tablet in a server room with floating glowing interface panels"></div>

<section class="welcome">
  <h1>WELCOME TO BEACON ADVISORY</h1>
  <div class="divider"></div>
  <p>Today's IT market is a dynamic, fast-paced industry, with ever-increasing demands. Meeting these demands for over 25 years, Beacon Advisory maintains a global presence, aggressively recruiting expertly qualified IT and Management Professionals from around the world and cultivating key partnerships with corporations to understand their business models end-to-end, with a goal of delivering exceptional client service and ensuring a consistent delivery of the talent needed to drive results.</p>
  <div class="more">+</div>
</section>

<article class="card" style="left:94px">
  <div class="card-head">
    <span class="card-icon"><svg width="20" height="20" viewBox="0 0 20 20"><circle cx="10" cy="10" r="4" fill="#fff"/><g stroke="#fff" stroke-width="1.6"><path d="M10 1v3M10 16v3M1 10h3M16 10h3M3.6 3.6l2 2M14.4 14.4l2 2M3.6 16.4l2-2M14.4 5.6l2-2"/></g></svg></span>
    <h2><b>IT</b> CONSULTING</h2>
  </div>
  <div class="card-photo" role="img" aria-label="Smiling professional working on a laptop at a bright office desk" style="background:linear-gradient(90deg,#9fb6cf,#e9ecef 60%,#cfd6dc)"></div>
  <p class="photo-text">Information technology should improve business results. Arvo helps companies make sure it does. We look at IT issues strategically, in the broader context of our clients' business. Our experts provide an objective, independent perspective to help companies realize the full potential of their IT resources, investments and assets.</p>
  <div class="card-plus">+</div>
</article>

<article class="card" style="left:428px;width:296px">
  <div class="card-head">
    <span class="card-icon"><svg width="18" height="20" viewBox="0 0 18 20"><rect x="2" y="2" width="13" height="16" rx="1.5" fill="none" stroke="#fff" stroke-width="1.6"/><path d="M5 7h7M5 10h7M5 13h4" stroke="#fff" stroke-width="1.4"/><circle cx="14" cy="16" r="3" fill="#fff"/></svg></span>
    <h2><b>WHAT</b> WE DO</h2>
  </div>
  <p class="intro-text">We are successful in deploying all students we trained into project with 2-3 weeks after training program. Our training programs will last for 6-8 weeks dependents on technology. We will provide on job support for trainees until technology comfort level is attained.</p>
  <ul class="services">
    <li><svg width="20" height="20" viewBox="0 0 20 20"><circle cx="8" cy="12" r="4.5" fill="none" stroke="#163f82" stroke-width="2"/><circle cx="15" cy="5" r="3" fill="none" stroke="#163f82" stroke-width="1.6"/></svg>Technology</li>
    <li><svg width="20" height="20" viewBox="0 0 20 20"><g fill="#163f82"><circle cx="4" cy="4" r="2"/><circle cx="10" cy="4" r="2"/><circle cx="16" cy="4" r="2"/><rect x="2.5" y="7" width="3" height="10"/><rect x="8.5" y="7" width="3" height="10"/><rect x="14.5" y="7" width="3" height="10"/></g></svg>Offshore Business</li>
    <li><svg width="20" height="20" viewBox="0 0 20 20"><rect x="4" y="1.5" width="11" height="17" rx="1.5" fill="none" stroke="#163f82" stroke-width="1.8"/><circle cx="9.5" cy="10" r="3" fill="#163f82"/></svg>Application Developement</li>
    <li><svg width="20" height="20" viewBox="0 0 20 20"><g fill="none" stroke="#163f82" stroke-width="1.6"><circle cx="10" cy="5" r="3"/><circle cx="5" cy="13" r="3"/><circle cx="15" cy="13" r="3"/></g></svg>Enterprise Integration</li>
    <li><svg width="20" height="20" viewBox="0 0 20 20"><circle cx="10" cy="10" r="5.5" fill="none" stroke="#163f82" stroke-width="2"/><circle cx="10" cy="10" r="2" fill="#163f82"/><path d="M10 1v3M10 16v3M1 10h3M16 10h3M3.6 3.6l2 2M14.4 14.4l2 2M3.6 16.4l2-2M14.4 5.6l2-2" stroke="#163f82" stroke-width="1.6"/></svg>IT Consulting</li>
  </ul>
  <div class="card-plus">+</div>
</article>

<article class="card" style="left:758px">
  <div class="card-head">
    <span class="card-icon"><svg width="20" height="20" viewBox="0 0 20 20"><circle cx="10" cy="10" r="5" fill="none" stroke="#fff" stroke-width="2"/><circle cx="10" cy="10" r="1.8" fill="#fff"/><path d="M10 1v3M10 16v3M1 10h3M16 10h3M3.6 3.6l2 2M14.4 14.4l2 2M3.6 16.4l2-2M14.4 5.6l2-2" stroke="#fff" stroke-width="1.6"/></svg></span>
    <h2><b>OFF</b>SHORE</h2>
  </div>
  <div class="card-photo" role="img" aria-label="Blue globe with glowing network connection lines across continents" style="background:radial-gradient(ellipse at 40% 60%,#5fb3e3,#1f6fae 60%,#0e3f78)"></div>
  <p class="photo-text">Our Offshore development model has a unique distinction of providing efficient software solutions with cost and quality advantage, using state-of-the-art technologies, having the capacity to handle large projects and, above all, the ability to execute timely deliveries.</p>
  <div class="card-plus">+</div>
</article>

<footer class="footer">
  <div class="footer-links">COMPANY<i>/</i>SERVICES<i>/</i>SOLUTIONS<i>/</i>RESOURCES<i>/</i>CAREER<i>/</i>CONTACT US</div>
  <div class="newsletter">
    <span class="nl-icon"><svg width="18" height="13" viewBox="0 0 18 13"><rect x="1" y="1" width="16" height="11" fill="none" stroke="#fff" stroke-width="1.6"/><path d="M1 1l8 6 8-6" fill="none" stroke="#fff" stroke-width="1.6"/></svg></span>
    <span class="nl-input">Sign Up for Newsletter</span>
    <span class="nl-btn">SUBSCRIBE</span>
  </div>
  <div class="social-foot" aria-label="Social links"><span></span><span></span><span></span><span></span></div>
  <div class="footer-brand"><span class="brand-mark"></span><span class="brand-name">BEACON ADVISORY</span></div>
  <div class="copyright">© 2016 &nbsp;BeaconAdvisory. All Right Reserved.</div>
</footer>
</body>
</html>
```